Business Card Re-Design/Update

We'd like to update out business cards. I've included our current "Style guide" which has the colour scheme of the organisation in it. I've also included the branding files with logos etc in them.

I've also included a copy of one of our existing cards so that you can see how ugly/dated they look. I'd like a fresh modern corporate look.

Target Market(s)

These are for our clients, potential clients, industry contacts - like all business cards

Contact Information for Business Card

Name
Position
Company Address - Level 1, 47 Fernby Street, Carlow Qld 4072
Direct Phone
mobile
Email
Website -www.korvalit.com.au
Logo

Colors

Designer to choose colors to be used in the design.

Requirements
Must have
• Main Logo
• Cards will need to be editable to be able to personalize them for each new employee.
Nice to have
• The MapOut, ShipWell, KeepSteady would be okay to have if they can be sensibly and professionally added to the look without detracting from the main imagery.
• Maybe they could go on the back of the card? will leave this to your creative discretion as to whether/where they fit.
Should not have
• Should not have decorative or script fonts

```html
<!DOCTYPE html>
<html lang="en">
<head>
<meta charset="utf-8">
<title>korvalIT business card</title>
<link rel="stylesheet" href="https://fonts.googleapis.com/css2?family=Work+Sans:wght@400;500;600&display=swap">
<style>
  :root {
    --backdrop: #2b2b2b;
    --card: #1b1b1b;
    --card-edge: #232323;
    --ink: #f2f2f2;
    --brand-red: #d7161d;
    --emboss: #3a3a3a;
  }
  * { margin: 0; padding: 0; box-sizing: border-box; }
  html, body {
    width: 1200px; height: 900px; overflow: hidden;
    background: var(--backdrop);
    font-family: "Work Sans", Arial, sans-serif;
  }
  .canvas { position: relative; width: 1200px; height: 900px; }
  .card {
    position: absolute; left: 280px; width: 640px; height: 391px;
    background: linear-gradient(160deg, var(--card-edge), var(--card) 60%);
    box-shadow: 0 6px 18px rgba(0,0,0,0.45);
  }
  .card--back { top: 45px; }
  .card--front { top: 464px; }

  .wordmark {
    display: flex; align-items: center; gap: 12px;
    font-weight: 600; letter-spacing: 0.5px; line-height: 1;
  }
  .wordmark__square { width: 30px; height: 30px; }
  .card--back .wordmark {
    position: absolute; left: 50%; top: 50%; transform: translate(-50%, -50%);
    font-size: 54px; color: var(--emboss);
  }
  .card--back .wordmark__square { background: var(--emboss); width: 38px; height: 38px; }

  .card--front .wordmark {
    position: absolute; left: 52px; top: 176px;
    font-size: 40px; color: var(--ink);
  }
  .card--front .wordmark__square { background: var(--brand-red); }

  .divider {
    position: absolute; left: 322px; top: 62px; width: 2px; height: 268px;
    background: var(--brand-red);
  }
  .details { position: absolute; left: 346px; top: 62px; color: var(--ink); }
  .details__name {
    font-size: 27px; font-weight: 500; color: var(--brand-red);
    text-transform: uppercase; letter-spacing: 0.5px; line-height: 1;
  }
  .details__role { font-size: 14px; letter-spacing: 0.6px; margin-top: 6px; }
  .details__address { font-size: 14.5px; letter-spacing: 0.6px; line-height: 1.3; margin-top: 14px; }
  .contacts { list-style: none; margin-top: 12px; }
  .contacts li {
    display: flex; align-items: center; gap: 10px;
    font-size: 15px; letter-spacing: 0.6px; line-height: 22px;
  }
  .contacts svg { width: 11px; height: 11px; fill: var(--brand-red); flex: none; }
</style>
</head>
<body>
<div class="canvas">

  <section class="card card--back" aria-label="Card back">
    <div class="wordmark"><span class="wordmark__square"></span><span>korvalIT</span></div>
  </section>

  <section class="card card--front" aria-label="Card front">
    <div class="wordmark"><span class="wordmark__square"></span><span>korvalIT</span></div>
    <div class="divider"></div>
    <div class="details">
      <p class="details__name">Maren Holt</p>
      <p class="details__role">Business Development Manager</p>
      <p class="details__address">Level 1, 47 Fernby Street,<br>Carlow Qld 4072</p>
      <ul class="contacts">
        <li><svg viewBox="0 0 12 12" aria-hidden="true"><path d="M3 0h6v12H3z M4 1v9h4V1z"/></svg>+61 (0)400 555 218</li>
        <li><svg viewBox="0 0 12 12" aria-hidden="true"><path d="M0 4q6-4 12 0v2H9V4.5H3V6H0z M2 7h8v4H2z"/></svg>+61 (0)7 5550 1416</li>
        <li><svg viewBox="0 0 12 12" aria-hidden="true"><path d="M2 0h3l1 3-2 1q1 3 4 4l1-2 3 1v3q-1 2-3 1Q2 9 1 3 0 1 2 0z"/></svg>+61 (0)7 5550 1400</li>
        <li><svg viewBox="0 0 12 12" aria-hidden="true"><path d="M3 0h6v3H3z M0 4h12v5H9v3H3V9H0z M4 8v3h4V8z"/></svg>+61 (0)7 5550 1403</li>
        <li><svg viewBox="0 0 12 12" aria-hidden="true"><path d="M0 2h12v8H0z M1 3v.5l5 3.5 5-3.5V3z"/></svg>mholt@korvalit.com.au</li>
        <li><svg viewBox="0 0 12 12" aria-hidden="true"><path d="M6 0a6 6 0 1 0 .01 0z M6 1.2A4.8 4.8 0 0 0 1.2 6h9.6A4.8 4.8 0 0 0 6 1.2z M1.4 6.8a4.8 4.8 0 0 0 9.2 0z"/></svg>www.korvalit.com.au</li>
      </ul>
    </div>
  </section>

</div>
</body>
</html>
```